Envelope Design - Winner can do follow-up business

- Varnoko.com is a Swiss-based online store selling business shirts and accessories for business men
- Please visit the webpage to make yourself familiar with the company. Although the text is in German, with Plimbo translator you should be able to understand the main content.
- Our clients are mainly business men between 30 and 60 years old. Mostly with a high income working in the service industry (banking, insurance, lawyers, etc.). Sometimes there wives purchase the shirts for them ;-)
- The colors and the logo are given, as they are also used for the print materials (please see files in attachment)
- I am running several businesses and often need a talented web designer --> the winner gets substantial follow-up business
your task:
-for our company we need a new envelope design
-It should be simple and modern
-please use one of the logos in the followings.
-suprise me :)

```html
<!DOCTYPE html>
<html lang="en">
<head>
<meta charset="utf-8">
<title>Varnoko Envelope Set</title>
<link rel="stylesheet" href="https://fonts.googleapis.com/css2?family=Roboto+Slab:wght@400;600&display=swap">
<style>
  :root {
    --bg: #e9e6e2;
    --paper: #ffffff;
    --paper-shade: #f3f3f5;
    --brand-red: #ee2e24;
    --brand-black: #000000;
    --brand-gold: #e2d363;
    --ink: #333333;
    --edge: #cfcfcf;
  }
  * { margin: 0; padding: 0; box-sizing: border-box; }
  html, body {
    width: 1200px;
    height: 925px;
    overflow: hidden;
    background: var(--bg);
    font-family: "Roboto Slab", serif;
  }
  .canvas {
    position: relative;
    width: 1200px;
    height: 925px;
  }
  .envelope {
    position: absolute;
    width: 1002px;
    height: 448px;
    background: var(--paper);
    box-shadow: 0 2px 6px rgba(0,0,0,0.18);
  }
  .envelope-back-red { left: 144px; top: 37px; }
  .envelope-back-black {
    left: 112px; top: 234px;
    background: linear-gradient(110deg, var(--paper-shade), var(--paper));
  }
  .envelope-front { left: 45px; top: 451px; }
  .flap { position: absolute; left: 0; top: 0; display: block; }
  .front-band {
    height: 44px;
    background: var(--brand-black);
    border-bottom: 5px solid var(--paper);
    box-shadow: 0 2px 0 var(--brand-red);
  }
  .sender {
    position: absolute;
    left: 22px;
    top: 74px;
  }
  .brand {
    display: flex;
    flex-direction: column;
    align-items: flex-start;
  }
  .brand-square {
    width: 44px;
    height: 44px;
    background: var(--brand-red);
    margin-left: 102px;
    margin-bottom: 12px;
  }
  .brand-name {
    font-size: 38px;
    font-weight: 600;
    letter-spacing: 3px;
    color: var(--brand-gold);
    line-height: 1;
  }
  .contact {
    list-style: none;
    margin-top: 14px;
    font-size: 15.5px;
    color: var(--ink);
  }
  .contact li {
    display: flex;
    align-items: center;
    gap: 12px;
    height: 30px;
  }
  .contact svg { width: 17px; height: 17px; flex: none; }
</style>
</head>
<body>
<main class="canvas">
  <section class="envelope envelope-back-red" aria-label="Envelope back, red flap">
    <svg class="flap" width="1002" height="180" viewBox="0 0 1002 180">
      <path d="M0 0 H1002 L990 40 Q980 88 930 98 L575 172 Q528 181 478 172 L72 98 Q22 88 12 40 Z" fill="var(--brand-red)"/>
    </svg>
  </section>

  <section class="envelope envelope-back-black" aria-label="Envelope back, black flap">
    <svg class="flap" width="1002" height="180" viewBox="0 0 1002 180">
      <path d="M0 0 H1002 L990 40 Q980 88 930 98 L575 168 Q528 178 478 168 L72 98 Q22 88 12 40 Z" fill="var(--brand-black)"/>
    </svg>
  </section>

  <section class="envelope envelope-front" aria-label="Envelope front">
    <div class="front-band"></div>
    <div class="sender">
      <div class="brand">
        <span class="brand-square"></span>
        <span class="brand-name">VARNOKO</span>
      </div>
      <ul class="contact">
        <li>
          <svg viewBox="0 0 24 24" aria-hidden="true"><path d="M12 2a7 7 0 0 0-7 7c0 5 7 13 7 13s7-8 7-13a7 7 0 0 0-7-7zm0 9.5A2.5 2.5 0 1 1 12 6.5a2.5 2.5 0 0 1 0 5z" fill="var(--brand-red)"/></svg>
          Street Name, City Name State Zipcode
        </li>
        <li>
          <svg viewBox="0 0 24 24" aria-hidden="true" fill="none" stroke="var(--brand-red)" stroke-width="1.6"><circle cx="12" cy="12" r="9"/><ellipse cx="12" cy="12" rx="4" ry="9"/><path d="M3 12h18M5 7h14M5 17h14"/></svg>
          www.varnoko.com
        </li>
      </ul>
    </div>
  </section>
</main>
</body>
</html>
```